RESIDENTIAL CONSTRUCTION

We are a company that specializes in building custom residential homes, the design should also emphasize that quality and service is our priority.

Industry/Entity Type

Construction Company

Contact Information for Business Card

Contact Person: Marcus Lindqvist
Company Address: 273 West Alder Ave San Jose , Ca 95380
Phone Number : 408-731-2946
Email Address: Stoneridgehomes517@mailvista.net

Font styles to use
Sans Serif

Colors
ec1f27

Requirements
Must have
• CSLB # 7362015
Nice to have
• needs to have same color as logo i uploaded, we will be printing these on a clear plastic card.

```html
<!DOCTYPE html>
<html lang="en">
<head>
<meta charset="utf-8">
<title>Stoneridge General Builders – Business Card</title>
<link rel="stylesheet" href="https://fonts.googleapis.com/css2?family=Oswald:wght@500&family=Open+Sans:wght@400;600&display=swap">
<style>
  :root {
    --backdrop: #2a2a2b;
    --card: #111112;
    --card-edge: #1e1e1f;
    --brand-red: #ec1f27;
    --name-ink: #d6d6d8;
    --text-muted: #9a9a9c;
    --divider: #ec1f27;
  }
  * { box-sizing: border-box; margin: 0; padding: 0; }
  html, body {
    width: 1200px; height: 716px; overflow: hidden;
    background: var(--backdrop);
  }
  .canvas {
    width: 1200px; height: 716px;
    display: flex; align-items: center; justify-content: center; gap: 40px;
  }
  .card {
    width: 540px; height: 309px;
    background: var(--card);
    border: 1px solid var(--card-edge);
    border-radius: 22px;
    position: relative;
    box-shadow: 0 18px 40px rgba(0,0,0,.45);
  }
  /* Front */
  .card-front { display: flex; align-items: center; justify-content: center; }
  .brand {
    display: flex; align-items: center; gap: 12px;
  }
  .brand-mark {
    width: 18px; height: 18px; background: var(--brand-red); flex: none;
  }
  .brand-name {
    font-family: "Open Sans", sans-serif; font-weight: 600;
    color: var(--brand-red);
    font-size: 26px; line-height: 1; white-space: nowrap;
  }
  /* Back */
  .card-back {
    padding: 0 26px;
    display: flex; align-items: center; justify-content: center;
  }
  .identity { text-align: right; padding-right: 14px; margin-top: -18px; }
  .person-name {
    font-family: "Oswald", sans-serif; font-weight: 500;
    font-size: 26px; letter-spacing: .3px;
    color: var(--name-ink);
    text-transform: uppercase; line-height: 1.1; white-space: nowrap;
  }
  .person-role {
    font-family: "Oswald", sans-serif; font-weight: 500;
    font-size: 14px; color: var(--brand-red);
    text-transform: uppercase; margin-top: 3px; letter-spacing: .3px;
    white-space: nowrap;
  }
  .divider {
    width: 2px; height: 70px; background: var(--divider); flex: none;
    margin-top: 22px;
  }
  .contact-list { list-style: none; padding-left: 12px; margin-top: 22px; }
  .contact-item {
    display: flex; align-items: center; gap: 8px;
    font-family: "Open Sans", sans-serif; font-size: 11.5px;
    color: var(--text-muted); line-height: 22px; white-space: nowrap;
  }
  .contact-icon { width: 11px; height: 11px; fill: var(--brand-red); flex: none; }
</style>
</head>
<body>
<main class="canvas">
  <section class="card card-front" aria-label="Card front">
    <div class="brand">
      <span class="brand-mark" aria-hidden="true"></span>
      <h1 class="brand-name">Stoneridge General Builders</h1>
    </div>
  </section>

  <section class="card card-back" aria-label="Card back">
    <div class="identity">
      <h2 class="person-name">Marcus Lindqvist</h2>
      <p class="person-role">Job Title | CSLB # 7362015</p>
    </div>
    <span class="divider" aria-hidden="true"></span>
    <ul class="contact-list">
      <li class="contact-item">
        <svg class="contact-icon" viewBox="0 0 24 24" aria-hidden="true"><path d="M6.6 10.8a15 15 0 0 0 6.6 6.6l2.2-2.2a1 1 0 0 1 1-.25 11.4 11.4 0 0 0 3.6.57 1 1 0 0 1 1 1V20a1 1 0 0 1-1 1A17 17 0 0 1 3 4a1 1 0 0 1 1-1h3.5a1 1 0 0 1 1 1c0 1.25.2 2.45.57 3.57a1 1 0 0 1-.25 1z"/></svg>
        408-731-2946
      </li>
      <li class="contact-item">
        <svg class="contact-icon" viewBox="0 0 24 24" aria-hidden="true"><path d="M2 5h20v14H2z M2 5l10 8 10-8" fill="none" stroke="#ec1f27" stroke-width="2.4"/></svg>
        Stoneridgehomes517@mailvista.net
      </li>
      <li class="contact-item">
        <svg class="contact-icon" viewBox="0 0 24 24" aria-hidden="true"><path d="M12 2a7 7 0 0 0-7 7c0 5.2 7 13 7 13s7-7.8 7-13a7 7 0 0 0-7-7zm0 9.5A2.5 2.5 0 1 1 12 6.5a2.5 2.5 0 0 1 0 5z"/></svg>
        273 West Alder Ave San Jose , Ca 95380
      </li>
    </ul>
  </section>
</main>
</body>
</html>
```